Website redesign for KestrelFinanceMan/TKFinanceMan

Job Title: Talented Web Designer for SEO-Friendly Website Creation & HostFalcon cPanel Integration
 
Inspiration: dunewheelracingexample.com
Pages:

About
Get a Quote
FAQ
Boat Loans
RV Loans
Testimonials
News/Blog
Affiliate Program
Contact

Job Description:
 
We are seeking a skilled and creative freelance web designer to build a stunning, SEO-optimized website for our business. The ideal candidate will have a strong design portfolio, technical expertise in creating search engine-friendly websites, and experience implementing websites into HostFalcon cPanel.
 
Project Overview:
 
Objective: Create a modern, motorsports themed visually appealing website that is optimized for SEO.

Platform: The site will be hosted on HostFalcon, so familiarity with their cPanel for setup and integration is essential.

Deliverables:
         •A fully functional website (desktop and mobile) with user-friendly navigation and a responsive design.
         •SEO best practices implemented throughout, including proper meta tags, optimized images, fast loading speeds, and mobile compatibility.
         •Seamless integration into HostFalcon cPanel for hosting.
         •Guidance or documentation on maintaining the site post-launch.
 
Key Skills Required:
 
         •Proficiency in web design (HTML, CSS, JavaScript, or relevant platforms like WordPress).
         •Knowledge of SEO principles and tools for website optimization.
         •Experience with HostFalcon cPanel, including file management and DNS settings.
         •Strong communication skills to understand our vision and provide progress updates.
 
What We’re Looking For:
 
         •A designer who can transform our ideas into a sleek and functional website.
         •Someone proactive in suggesting creative design elements and SEO improvements.
         •A reliable professional who can meet deadlines and deliver a polished product.
 
Please provide:
 
         1.A brief introduction and why you’re a good fit for this project.
         2.Examples of previous web design projects, especially those with SEO implementation.
         3.Your estimated timeline and cost for this project.
 
We are excited to work with a talented designer who can bring our vision to life. If you are passionate about web design and SEO, we’d love to hear from you!

Target Market(s)

Boat and RV buyers looking for a loan

Coding

Coded - Design and coding required

Number of Pages Required

5+ page

Colors
F0912C
F2A743
F7CA91
FBE8D2
FDF5EE

Requirements
Must have
• motorsports type design
Nice to have
• fcontact forms easy to use layout on brand and color scheme of kestrelfinanceman and tkfinanceman.example

```html
<!DOCTYPE html>
<html lang="en">
<head>
<meta charset="utf-8">
<title>TKFinanceMan – RV Loans Made Easy</title>
<link href="https://fonts.googleapis.com/css2?family=Oswald:wght@500;600;700&family=Open+Sans:wght@400;600;700&display=swap" rel="stylesheet">
<style>
:root{
  --orange:#F0912C;
  --orange-2:#F2A743;
  --orange-3:#F7CA91;
  --cream:#FBE8D2;
  --cream-2:#FDF5EE;
  --ink:#2b2b2b;
  --muted:#6a6a6a;
  --dark:#4a4a4c;
  --darker:#333335;
  --white:#ffffff;
}
*{box-sizing:border-box;margin:0;padding:0}
html,body{width:1200px;height:4512px;overflow:hidden}
body{position:relative;background:var(--white);font-family:"Open Sans",Arial,sans-serif;color:var(--ink)}
.abs{position:absolute}
.title{font-family:"Oswald",Arial,sans-serif;font-weight:600;text-transform:uppercase;letter-spacing:1px}
.center{text-align:center;left:0;width:1200px}

/* header */
.topbar{top:0;left:0;width:1200px;height:150px;z-index:5}
.badge{left:120px;top:18px;width:64px;height:64px;border-radius:50%;background:var(--orange-3)}
.badge-text{left:196px;top:28px;font-size:14px;font-weight:700;color:var(--white);line-height:18px}
.logo{left:430px;top:8px;width:340px;height:72px;border-radius:36px;background:var(--white);display:flex;align-items:center;justify-content:center;gap:12px;box-shadow:0 4px 10px rgba(0,0,0,.25)}
.logo .dot{width:26px;height:26px;border-radius:50%;background:var(--orange)}
.logo span{font-family:"Oswald",Arial,sans-serif;font-weight:700;font-size:38px;color:var(--orange)}
.call{left:860px;top:18px;display:flex;gap:12px;align-items:center}
.call .ico{width:44px;height:44px;border-radius:50%;background:var(--orange);display:flex;align-items:center;justify-content:center}
.call small{display:block;font-size:14px;font-weight:700;color:var(--white)}
.call b{font-size:22px;color:var(--orange)}
.nav{left:130px;top:86px;display:flex;align-items:center;gap:26px;font-size:14px;font-weight:700;color:var(--white);text-transform:uppercase}
.nav .active{background:var(--orange);padding:10px 14px;border-radius:4px}
.nav .apply{background:var(--orange);padding:10px 22px;border-radius:22px;margin-left:10px}

/* hero */
.hero{top:0;left:0;width:1200px;height:800px;background:linear-gradient(180deg,#2c3340 0%,#b8652d 30%,#e39a4d 42%,#5a6f82 60%,#2f4a63 100%)}
.hero-h1{top:318px;font-size:58px;color:var(--white);font-weight:700}
.hero-sub{top:402px;font-size:24px;font-weight:700;color:var(--white)}
.quote-bar{left:200px;top:448px;width:800px;height:76px;background:rgba(40,40,40,.85);display:flex;align-items:center;gap:14px;padding:0 16px}
.quote-bar .field{width:200px;height:42px;background:var(--white);font-size:13px;color:var(--muted);display:flex;align-items:center;padding-left:12px}
.quote-bar .btn{height:42px;padding:0 30px;background:var(--orange);color:var(--white);font-weight:700;font-size:15px;border-radius:21px;display:flex;align-items:center}
.hero-dots{left:1124px;top:440px;display:flex;flex-direction:column;gap:12px}
.hero-dots i{width:12px;height:12px;border-radius:50%;background:rgba(255,255,255,.6)}
.hero-dots i:first-child{background:var(--white)}
.hero-rv{left:0;top:300px;width:440px;height:460px;background:linear-gradient(160deg,#d8d4cc,#8a857c);border-radius:30px 120px 20px 20px;opacity:.9}
.hero-wave{left:0;top:640px}

/* finance */
.sec-title{font-size:68px;color:#3a3a3a}
.finance-title{top:820px}
.finance-sub{top:944px;font-size:22px;font-style:italic;font-weight:600}
.finance-text{top:994px;font-size:19px;line-height:30px;color:var(--muted)}
.fin-card{top:1070px;width:270px;height:270px;border-radius:50%;border:6px solid var(--white);box-shadow:0 4px 14px rgba(0,0,0,.2)}
.fin-label{top:1312px;width:240px;height:56px;border-radius:28px;background:var(--white);box-shadow:0 4px 12px rgba(0,0,0,.15);font-weight:700;font-size:16px;display:flex;align-items:center;justify-content:center}
.fin-label.on{background:var(--orange);color:var(--white)}
.fin-contact{left:505px;top:1190px;width:190px;height:46px;border-radius:23px;background:rgba(255,255,255,.9);font-weight:700;font-size:15px;color:var(--orange);display:flex;align-items:center;justify-content:center;text-decoration:underline}

/* about */
.about-band{left:0;top:1380px}
.about-title{left:150px;top:1570px;font-size:68px;color:var(--white)}
.about-lead{left:150px;top:1680px;font-size:22px;color:var(--white)}
.about-list{left:170px;top:1730px;font-size:16px;line-height:28px;color:var(--white);list-style:disc}
.about-text{left:150px;top:1920px;width:460px;font-size:16px;line-height:26px;color:var(--white)}
.about-photo{left:600px;top:1600px;width:430px;height:430px;border-radius:50%;border:8px solid var(--white);background:radial-gradient(circle at 40% 40%,#8bb7cf,#4a86a6 60%,#7a6e4c)}
.about-boat{left:740px;top:2040px;width:360px;height:150px;background:linear-gradient(90deg,#2a3b6a,#3a4a7c,#1d2a4d);border-radius:70px 20px 30px 90px}

/* apply */
.apply-title{top:2250px}
.apply-sub{top:2374px;font-size:22px;font-style:italic;font-weight:600}
.cats{left:100px;top:2460px;width:1000px;display:flex;justify-content:space-between;align-items:flex-start}
.cat{width:156px;text-align:center;font-size:20px;font-weight:600}
.cat .ring{width:150px;height:150px;border-radius:50%;border:3px solid var(--orange-3);display:flex;align-items:center;justify-content:center;margin:0 auto 16px}
.cat.on .ring{border:6px solid var(--orange)}
.arrow{width:44px;height:44px;border-radius:50%;border:2px solid #bdbdbd;background:var(--white);display:flex;align-items:center;justify-content:center}
.apply-btn{left:510px;top:2690px;width:180px;height:50px;border-radius:25px;background:var(--orange);color:var(--white);font-weight:700;font-size:15px;display:flex;align-items:center;justify-content:center}

/* reviews */
.rev-bg{left:0;top:2730px;width:1200px;height:840px;background:linear-gradient(180deg,var(--white) 0%,var(--cream) 30%,var(--cream-2) 75%,var(--white) 100%)}
.rev-boat{left:60px;top:2740px;width:520px;height:290px;background:linear-gradient(135deg,#e9e9e9,#9da3a8 60%,#34393d);border-radius:40px 220px 60px 160px}
.rev-title{top:3020px}
.rev-sub{top:3142px;font-size:22px;font-style:italic;font-weight:600}
.rev-quote{left:250px;top:3196px;width:700px;font-size:16px;line-height:27px;color:var(--muted);text-align:center}
.rev-name{top:3338px;font-size:17px;font-weight:600;letter-spacing:1px}
.rev-name b{color:var(--orange);letter-spacing:3px;margin-left:10px}

/* clients */
.cli-title{top:3594px}
.clients{left:100px;top:3758px;width:1000px;display:flex;align-items:center;gap:22px}
.client{width:200px;height:96px;border-radius:48px;background:var(--white);box-shadow:0 3px 12px rgba(0,0,0,.15);display:flex;align-items:center;justify-content:center;font-weight:700;font-size:24px;color:#3a3a3a}
.client.on{border:4px solid var(--orange)}

/* footer */
.foot{left:0;top:3870px}
.foot-rv{left:390px;top:3890px;width:420px;height:280px;background:linear-gradient(160deg,#f3f1ec,#b9b6ae);border-radius:40px 40px 20px 20px}
.fcol{top:4176px;color:var(--white)}
.fcol h4{font-family:"Oswald",Arial,sans-serif;font-weight:600;font-size:24px;margin-bottom:22px}
.fcol p{font-size:15px;line-height:26px;display:flex;gap:10px;margin-bottom:8px}
.links{display:grid;grid-template-columns:150px 150px;font-size:15px;line-height:28px}
.form-row{display:flex;gap:12px;margin-bottom:12px}
.form-row div,.form-msg{background:var(--white);height:40px;width:140px;font-size:12px;color:var(--muted);padding:10px}
.form-msg{width:292px;height:72px}
.form-btn{margin-top:12px;width:94px;height:36px;border-radius:18px;background:var(--orange);font-size:13px;font-weight:700;display:flex;align-items:center;justify-content:center}
.socials{display:flex;gap:10px;margin-top:10px}
.socials i{width:34px;height:34px;border-radius:50%;background:var(--white)}
.socials i:nth-child(2){background:var(--orange)}
.copy{top:4448px;font-size:15px;color:var(--white)}
</style>
</head>
<body>

<!-- HERO -->
<div class="abs hero" role="img" aria-label="Sunset over calm water with a luxury motorhome on the shoreline"></div>
<div class="abs hero-rv" role="img" aria-label="Luxury class A motorhome"></div>
<svg class="abs hero-wave" width="1200" height="170" viewBox="0 0 1200 170">
  <path d="M0 90 C150 40 300 150 470 110 C640 70 760 20 900 70 C1020 115 1110 60 1200 40 V170 H0Z" fill="#fff"/>
  <path d="M0 90 C150 40 300 150 470 110 C640 70 760 20 900 70 C1020 115 1110 60 1200 40" fill="none" stroke="#9a9a9a" stroke-width="6" stroke-dasharray="18 12"/>
</svg>

<header class="abs topbar">
  <div class="abs badge"></div>
  <div class="abs badge-text">BASED ON<br>1000 REVIEWS</div>
  <div class="abs logo"><i class="dot"></i><span>TKFinanceMan</span></div>
  <div class="abs call">
    <div class="ico"><svg width="22" height="22" viewBox="0 0 24 24"><path d="M6.6 10.8a15 15 0 0 0 6.6 6.6l2.2-2.2c.3-.3.7-.4 1-.2 1.1.4 2.3.6 3.6.6.6 0 1 .4 1 1V20c0 .6-.4 1-1 1A17 17 0 0 1 3 4c0-.6.4-1 1-1h3.5c.6 0 1 .4 1 1 0 1.3.2 2.5.6 3.6.1.3 0 .7-.2 1z" fill="#fff"/></svg></div>
    <div><small>CALL US TODAY!</small><b>555-014-2290</b></div>
  </div>
  <nav class="abs nav">
    <span class="active">Home</span><span>About</span><span>Get a Quote</span><span>FAQ</span><span>Boat Loans</span><span>RV Loans</span><span>Testimonials</span><span>News</span><span>Affiliate Program</span><span>Contact</span><span class="apply">Apply Now</span>
  </nav>
</header>

<h1 class="abs center title hero-h1">RV Loans Made Easy!</h1>
<p class="abs center hero-sub">Your one-stop resource for all of your RV financing needs.</p>
<div class="abs quote-bar">
  <div class="field">Loan Amount</div><div class="field">Rate (APR)</div><div class="field">Term (years)</div><div class="btn">APPLY NOW</div>
</div>
<div class="abs hero-dots"><i></i><i></i><i></i></div>

<!-- FINANCE -->
<h2 class="abs center title sec-title finance-title">Finance</h2>
<p class="abs center finance-sub">We finance more than just boats</p>
<p class="abs center finance-text">At Harbor Crest Finance, we are your one-stop resource for<br>all marine, RV and Airplane Financing</p>
<div class="abs fin-card" style="left:150px;background:linear-gradient(160deg,#7fb7d6,#c8452c 55%,#2f6f9b)" role="img" aria-label="Speed boat on open water"></div>
<div class="abs fin-card" style="left:465px;background:linear-gradient(160deg,#c9d6de,#f0ede6 50%,#8f8575)" role="img" aria-label="Motorhome parked outdoors"></div>
<div class="abs fin-card" style="left:780px;background:linear-gradient(160deg,#a9cbe6,#ffffff 55%,#9aa3ab)" role="img" aria-label="Private jet on the runway"></div>
<div class="abs fin-contact">CONTACT US</div>
<div class="abs fin-label" style="left:165px">MARINE FINANCING</div>
<div class="abs fin-label on" style="left:480px">RV FINANCING</div>
<div class="abs fin-label" style="left:795px">AIRCRAFT FINANCING</div>

<!-- ABOUT -->
<svg class="abs about-band" width="1200" height="860" viewBox="0 0 1200 860">
  <defs><linearGradient id="aboutGrad" x1="0" y1="0" x2="1" y2="1"><stop offset="0" stop-color="#F2A743"/><stop offset="1" stop-color="#F0912C"/></linearGradient></defs>
  <path d="M0 70 C200 10 380 120 600 70 C820 20 1000 110 1200 40 V790 C1000 860 820 760 600 810 C380 860 200 770 0 820Z" fill="url(#aboutGrad)"/>
  <path d="M0 70 C200 10 380 120 600 70 C820 20 1000 110 1200 40" fill="none" stroke="#FBE8D2" stroke-width="5" stroke-dasharray="16 12"/>
</svg>
<h2 class="abs title about-title">About Us</h2>
<p class="abs about-lead">Your trusted source for RV Financing</p>
<ul class="abs about-list">
  <li>Loans from $15,000 - $5M</li>
  <li>Up to 20yrs on RVs</li>
  <li>Same Day Approvals</li>
  <li>Quick Funding</li>
  <li>Private Party or Dealer</li>
  <li>Bad Credit is OK</li>
</ul>
<p class="abs about-text">Our goal is to make your RV purchase as quick and stress-free as possible. Our numerous lender relationships allow us to offer competitive rates and terms with quick turn-around times.</p>
<div class="abs about-photo" role="img" aria-label="Aerial view of boats on a blue lake"></div>
<div class="abs about-boat" role="img" aria-label="Bass fishing boat on a trailer"></div>

<!-- APPLY -->
<h2 class="abs center title sec-title apply-title">Apply Now</h2>
<p class="abs center apply-sub">We finance ALL Types of RV's</p>
<div class="abs arrow" style="left:50px;top:2520px"><svg width="14" height="14" viewBox="0 0 14 14"><path d="M9 2 4 7l5 5" stroke="#777" stroke-width="2" fill="none"/></svg></div>
<div class="abs arrow" style="left:1106px;top:2520px"><svg width="14" height="14" viewBox="0 0 14 14"><path d="m5 2 5 5-5 5" stroke="#777" stroke-width="2" fill="none"/></svg></div>
<div class="abs cats">
  <div class="cat on"><div class="ring"><svg width="80" height="56" viewBox="0 0 80 56" fill="none" stroke="#F0912C" stroke-width="3"><rect x="4" y="8" width="72" height="36" rx="6"/><rect x="12" y="16" width="18" height="12"/><rect x="38" y="16" width="30" height="12"/><circle cx="20" cy="46" r="6"/><circle cx="60" cy="46" r="6"/></svg></div>Diesel Pushers</div>
  <div class="cat"><div class="ring"><svg width="80" height="56" viewBox="0 0 80 56" fill="none" stroke="#333" stroke-width="3"><rect x="4" y="10" width="72" height="34" rx="4"/><rect x="10" y="16" width="16" height="12"/><rect x="32" y="16" width="14" height="22"/><circle cx="20" cy="46" r="6"/><circle cx="60" cy="46" r="6"/></svg></div>Class A</div>
  <div class="cat"><div class="ring"><svg width="80" height="56" viewBox="0 0 80 56" fill="none" stroke="#333" stroke-width="3"><path d="M4 44V14h50l20 14v16z"/><rect x="12" y="20" width="14" height="10"/><path d="M56 18 70 28H56z"/><circle cx="20" cy="46" r="6"/><circle cx="60" cy="46" r="6"/></svg></div>Class B</div>
  <div class="cat"><div class="ring"><svg width="80" height="56" viewBox="0 0 80 56" fill="none" stroke="#333" stroke-width="3"><path d="M4 44V6h54v10h10l8 12v16z"/><rect x="12" y="14" width="16" height="12"/><circle cx="20" cy="46" r="6"/><circle cx="60" cy="46" r="6"/></svg></div>Class C</div>
  <div class="cat"><div class="ring"><svg width="80" height="56" viewBox="0 0 80 56" fill="none" stroke="#333" stroke-width="3"><path d="M4 40V10h60v30zM64 30h12"/><rect x="12" y="16" width="16" height="10"/><rect x="40" y="16" width="16" height="24"/><circle cx="26" cy="44" r="6"/><circle cx="40" cy="44" r="6"/></svg></div>Toy Haulers</div>
</div>
<div class="abs apply-btn">APPLY NOW</div>

<!-- REVIEWS -->
<div class="abs rev-bg"></div>
<div class="abs rev-boat" role="img" aria-label="Wake surf boat cruising on a lake"></div>
<h2 class="abs center title sec-title rev-title">Reviews</h2>
<p class="abs center rev-sub">What our Customers say</p>
<div class="abs arrow" style="left:130px;top:3250px"><svg width="14" height="14" viewBox="0 0 14 14"><path d="M9 2 4 7l5 5" stroke="#777" stroke-width="2" fill="none"/></svg></div>
<div class="abs arrow" style="left:1026px;top:3250px"><svg width="14" height="14" viewBox="0 0 14 14"><path d="m5 2 5 5-5 5" stroke="#777" stroke-width="2" fill="none"/></svg></div>
<p class="abs rev-quote">"Just purchased a boat and used the team and they made the process very easy. Jenna Holt helped every step of the way and was always available when I had any questions. She was quick to keep me updated and streamlined the entire process of paperwork and funding. I would highly recommend using this team based on my purchasing experience.</p>
<p class="abs center rev-name">DELIA MARSH <b>★★★★★</b></p>

<!-- CLIENTS -->
<h2 class="abs center title sec-title cli-title">Our Clients</h2>
<div class="abs clients">
  <div class="arrow"><svg width="14" height="14" viewBox="0 0 14 14"><path d="M9 2 4 7l5 5" stroke="#777" stroke-width="2" fill="none"/></svg></div>
  <div class="client">Trailcrest</div>
  <div class="client on">Roamwell</div>
  <div class="client">Dunefox</div>
  <div class="client">Skyhaven</div>
  <div class="arrow"><svg width="14" height="14" viewBox="0 0 14 14"><path d="m5 2 5 5-5 5" stroke="#777" stroke-width="2" fill="none"/></svg></div>
</div>

<!-- FOOTER -->
<svg class="abs foot" width="1200" height="642" viewBox="0 0 1200 642">
  <path d="M0 80 C200 20 380 120 600 70 C820 20 1000 110 1200 50 V642 H0Z" fill="#4a4a4c"/>
  <path d="M0 80 C200 20 380 120 600 70 C820 20 1000 110 1200 50" fill="none" stroke="#bdbdbd" stroke-width="5" stroke-dasharray="16 12"/>
  <rect x="0" y="558" width="1200" height="84" fill="#333335"/>
</svg>
<div class="abs foot-rv" role="img" aria-label="Class C motorhome"></div>

<div class="abs fcol" style="left:140px">
  <h4>CONTACT US</h4>
  <p><svg width="16" height="16" viewBox="0 0 24 24"><path d="M6.6 10.8a15 15 0 0 0 6.6 6.6l2.2-2.2c.3-.3.7-.4 1-.2 1.1.4 2.3.6 3.6.6.6 0 1 .4 1 1V20c0 .6-.4 1-1 1A17 17 0 0 1 3 4c0-.6.4-1 1-1h3.5c.6 0 1 .4 1 1 0 1.3.2 2.5.6 3.6.1.3 0 .7-.2 1z" fill="#F0912C"/></svg>(555) 014-2290</p>
  <p><svg width="16" height="16" viewBox="0 0 24 24"><rect x="2" y="5" width="20" height="14" fill="none" stroke="#F0912C" stroke-width="2"/><path d="m2 6 10 7 10-7" fill="none" stroke="#F0912C" stroke-width="2"/></svg>info@tkfinanceman.example</p>
  <p><svg width="16" height="16" viewBox="0 0 24 24"><path d="M12 2a7 7 0 0 0-7 7c0 5 7 13 7 13s7-8 7-13a7 7 0 0 0-7-7zm0 9.5A2.5 2.5 0 1 1 12 6.5a2.5 2.5 0 0 1 0 5z" fill="#F0912C"/></svg>4410 Meridian Way Ste 210,<br>Lakeview, CA 90000</p>
  <div class="socials"><i></i><i></i><i></i></div>
</div>
<div class="abs fcol" style="left:470px">
  <h4>QUICK LINKS</h4>
  <div class="links"><span>About</span><span>Testimonials</span><span>Get a Quote</span><span>News/Blog</span><span>FAQ</span><span>Affiliate Program</span><span>Boat Loans</span><span>Contact</span><span>RV Loans</span></div>
</div>
<div class="abs fcol" style="left:790px">
  <h4>GET A QUOTE</h4>
  <div class="form-row"><div>Enter Name</div><div>Enter Email</div></div>
  <div class="form-msg">Message</div>
  <div class="form-btn">SUBMIT</div>
</div>
<p class="abs center copy">Copyright © 2024 TKFinanceMan. All Rights Reserved &nbsp;|&nbsp; Privacy Policy &nbsp;|&nbsp; Terms of use</p>

</body>
</html>
```